Roadside building business signage for a holistic health clinic.

Replace signs as shown in the attached file. They are perforated stickers that go on the windows as shown. Looking for something that has our logo and says the name of the practice with logo (Fernridge Health & Wellness) also boldly says Acupuncture, IV Vitamins, and Holistic Health.
Possibly our phone number as well 318-562-7041
Updates

Please don't use pink except the logo. Earthy, organic tone colors appreciated.

Need of eye catching window signage of a holistic clinic on a brick building. Pink, purple, sage green, white color. Logo is pink on a white background. Please don't overload with too much pink. Words to include are "Fernridge Health and Wellness(name of business)", "Direct Primary Care", " Medical acupuncture", "IV Vitamin Therapy", "fernridgecareclinic.example","318-562-7041".

Target Market(s)

People will see in their cars passing by the building. Busy roadside so need to be visible while passing in fast speed.

Industry/Entity Type

Health & Wellness

Font styles to use
Sans Serif

Colors

Designer to choose colors to be used in the design.

Requirements
Must have
• On sign must have words Holistic Medicine, Medical Acupuncture, Direct Primary Care and IV vitamins.
Nice to have
• Simple, minimalistic, artistic yet has clear message. White, Black, Violet, Pink (logo), Dark green, Sage green.
Should not have
• Bold colors (red, yellow, blue), same tone colors. Blue waves on the current signage (uploaded file) must go.

```html
<!DOCTYPE html>
<html lang="en">
<head>
<meta charset="utf-8">
<title>Fernridge Health &amp; Wellness — Window Sign</title>
<link rel="stylesheet" href="https://fonts.googleapis.com/css2?family=Bebas+Neue&display=swap">
<style>
  :root {
    --backdrop: #5b5b5b;
    --forest: #07302a;
    --cream: #f3e8d8;
    --paper-edge: #ffffff;
    --blossom: #e0407f;
  }
  html, body {
    margin: 0;
    padding: 0;
    width: 1200px;
    height: 2269px;
    overflow: hidden;
    background: var(--backdrop);
  }
  .canvas {
    position: relative;
    width: 1200px;
    height: 2269px;
  }
  .window-sign {
    position: absolute;
    left: 60px;
    top: 865px;
    width: 1080px;
    height: 539px;
    background: var(--forest);
    overflow: hidden;
    font-family: "Bebas Neue", "Arial Narrow", sans-serif;
  }
  .torn-panel {
    position: absolute;
    inset: 0;
    width: 1080px;
    height: 539px;
  }
  .service {
    position: absolute;
    left: 41px;
    margin: 0;
    color: var(--cream);
    font-size: 60px;
    line-height: 1;
    font-weight: 400;
    white-space: nowrap;
  }
  .service--holistic { top: 30px; }
  .service--primary { top: 100px; }
  .service--acupuncture { top: 170px; }
  .service--vitamins { top: 240px; }
  .service-rule {
    position: absolute;
    left: 41px;
    width: 366px;
    height: 2px;
    background: var(--cream);
    opacity: 0.85;
  }
  .service-rule--first { top: 89px; }
  .service-rule--second { top: 159px; }
  .service-rule--third { top: 229px; }
  .contact-label {
    position: absolute;
    left: 41px;
    top: 328px;
    margin: 0;
    color: var(--cream);
    font-size: 36px;
    line-height: 1;
    white-space: nowrap;
  }
  .contact-dash {
    position: absolute;
    left: 195px;
    top: 343px;
    width: 58px;
    height: 3px;
    background: var(--cream);
  }
  .contact-phone {
    position: absolute;
    left: 41px;
    top: 370px;
    margin: 0;
    color: var(--cream);
    font-size: 64px;
    line-height: 1;
    white-space: nowrap;
  }
  .contact-web {
    position: absolute;
    left: 41px;
    top: 448px;
    margin: 0;
    color: var(--cream);
    font-size: 30px;
    line-height: 1;
    letter-spacing: 1px;
    white-space: nowrap;
  }
  .brand {
    position: absolute;
    left: 600px;
    width: 420px;
    top: 120px;
    margin: 0;
    text-align: center;
    color: var(--forest);
    font-weight: 400;
  }
  .brand-dot {
    display: block;
    width: 100px;
    height: 100px;
    margin: 0 auto 30px;
    border-radius: 50%;
    background: var(--blossom);
  }
  .brand-name {
    display: block;
    font-size: 76px;
    line-height: 1;
    letter-spacing: 6px;
    white-space: nowrap;
  }
  .brand-tagline {
    display: block;
    margin-top: 8px;
    font-size: 34px;
    line-height: 1;
    letter-spacing: 5px;
    white-space: nowrap;
  }
</style>
</head>
<body>
<main class="canvas">
  <section class="window-sign" aria-label="Fernridge Health &amp; Wellness window sign">
    <svg class="torn-panel" viewBox="0 0 1080 539" aria-hidden="true">
      <path fill="var(--cream)" stroke="var(--paper-edge)" stroke-width="3"
        d="M696 0 L1080 0 L1080 539 L410 539
           L414 520 L420 512 L418 498 L426 484 L431 457
           L446 450 L458 438 L470 430 L480 418 L493 405
           L500 394 L508 386 L512 376 L519 369
           L526 358 L530 346 L536 334 L544 322 L550 306
           L558 300 L563 290 L566 276 L572 266 L576 246
           L584 236 L590 220 L598 202 L604 190 L608 178
           L616 158 L626 146 L632 132 L640 124 L646 112 L651 106
           L654 92 L660 80 L662 64 L668 44 L676 34 L682 20 L690 12 Z"/>
    </svg>

    <h2 class="service service--holistic">Holistic Medicine</h2>
    <div class="service-rule service-rule--first"></div>
    <h2 class="service service--primary">Direct Primary Care</h2>
    <div class="service-rule service-rule--second"></div>
    <h2 class="service service--acupuncture">Medical Acupuncture</h2>
    <div class="service-rule service-rule--third"></div>
    <h2 class="service service--vitamins">IV Vitamins</h2>

    <p class="contact-label">Contact Us</p>
    <div class="contact-dash"></div>
    <p class="contact-phone">318-562-7041</p>
    <p class="contact-web">fernridgecareclinic.example</p>

    <h1 class="brand">
      <span class="brand-dot"></span>
      <span class="brand-name">Fernridge</span>
      <span class="brand-tagline">Health &amp; Wellness</span>
    </h1>
  </section>
</main>
</body>
</html>
```